Harborline Auto LLC

Car Dealer Customer Service
Address: 2874 Cresthaven Road, Shelbyville, TN 37162
web: www.harborlineautoxq.net
email: harborlineautoxq@mailnest.example
Phone: (931) 555-0148
Phone: (629) 555-0173

```html
<!DOCTYPE html>
<html lang="en">
<head>
<meta charset="utf-8">
<title>Harborline Auto LLC – Business Card</title>
<link rel="stylesheet" href="https://fonts.googleapis.com/css2?family=Montserrat:wght@400;700;800&display=swap">
<style>
  :root {
    --backdrop: #e8e9eb;
    --card: #ffffff;
    --brand-blue: #1f77b4;
    --accent-blue: #2b93d6;
    --ink: #1c1c1c;
    --shadow: rgba(0, 0, 0, 0.12);
  }
  * { margin: 0; padding: 0; box-sizing: border-box; }
  html, body {
    width: 1200px;
    height: 900px;
    overflow: hidden;
    background: var(--backdrop);
    font-family: "Montserrat", sans-serif;
  }
  .canvas {
    position: relative;
    width: 1200px;
    height: 900px;
  }
  .card {
    position: absolute;
    width: 560px;
    height: 320px;
    background: var(--card);
    box-shadow: 0 10px 28px var(--shadow);
    overflow: hidden;
  }
  .card--front { left: 120px; top: 90px; }
  .card--back { left: 520px; top: 490px; }

  .brand {
    display: flex;
    align-items: center;
    gap: 14px;
    color: var(--brand-blue);
    font-weight: 800;
    text-transform: uppercase;
    letter-spacing: 0.02em;
    line-height: 1;
  }
  .brand__dot {
    flex: none;
    border-radius: 50%;
    background: var(--accent-blue);
  }
  .card--front .brand {
    position: absolute;
    left: 0; right: 0; top: 0; bottom: 0;
    justify-content: center;
    font-size: 34px;
  }
  .card--front .brand__dot { width: 60px; height: 60px; }

  .card--back .brand {
    position: absolute;
    left: 48px;
    top: 92px;
    font-size: 22px;
    gap: 10px;
  }
  .card--back .brand__dot { width: 40px; height: 40px; }

  .address {
    position: absolute;
    right: 60px;
    top: 40px;
    text-align: right;
    font-size: 13px;
    line-height: 1.45;
    color: var(--ink);
  }
  .address__bar {
    position: absolute;
    right: 0;
    top: 38px;
    width: 22px;
    height: 60px;
    background: var(--accent-blue);
  }

  .contact-list {
    position: absolute;
    left: 48px;
    bottom: 34px;
    list-style: none;
    font-size: 13.5px;
    color: var(--ink);
  }
  .contact-list__item {
    display: flex;
    align-items: center;
    gap: 10px;
    height: 24px;
  }
  .contact-list__icon {
    width: 13px;
    height: 13px;
    flex: none;
    fill: var(--accent-blue);
  }
</style>
</head>
<body>
<main class="canvas">

  <section class="card card--front" aria-label="Card front">
    <div class="brand">
      <span class="brand__dot"></span>
      <span class="brand__name">Harborline Auto</span>
    </div>
  </section>

  <section class="card card--back" aria-label="Card back">
    <div class="address">
      <p>Car Dealer Customer Service</p>
      <p>2874 Cresthaven Road</p>
      <p>Shelbyville, TN 37162</p>
    </div>
    <span class="address__bar"></span>

    <div class="brand">
      <span class="brand__dot"></span>
      <span class="brand__name">Harborline Auto</span>
    </div>

    <ul class="contact-list">
      <li class="contact-list__item">
        <svg class="contact-list__icon" viewBox="0 0 16 16" aria-hidden="true">
          <path d="M3 1h3l1.5 4-2 1.3a9 9 0 0 0 4.2 4.2L11 8.5l4 1.5v3a2 2 0 0 1-2 2A13 13 0 0 1 1 3a2 2 0 0 1 2-2z"/>
        </svg>
        <span>(931) 555-0148</span>
      </li>
      <li class="contact-list__item">
        <svg class="contact-list__icon" viewBox="0 0 16 16" aria-hidden="true">
          <path d="M1 5c0-2 3-3 7-3s7 1 7 3v1h-3V4.5H4V6H1z"/>
          <path d="M3 8l2-2h6l2 2v6H3z"/>
        </svg>
        <span>(629) 555-0173</span>
      </li>
      <li class="contact-list__item">
        <svg class="contact-list__icon" viewBox="0 0 16 16" aria-hidden="true">
          <path d="M1 3h14v10H1z M2 4l6 5 6-5" fill="var(--accent-blue)"/>
          <path d="M2 4.2l6 4.8 6-4.8" fill="none" stroke="#fff" stroke-width="1.2"/>
        </svg>
        <span>harborlineautoxq@mailnest.example</span>
      </li>
      <li class="contact-list__item">
        <svg class="contact-list__icon" viewBox="0 0 16 16" aria-hidden="true">
          <circle cx="8" cy="8" r="7"/>
          <path d="M1 8h14M8 1c-3 3-3 11 0 14M8 1c3 3 3 11 0 14" fill="none" stroke="#fff" stroke-width="1"/>
        </svg>
        <span>www.harborlineautoxq.net</span>
      </li>
    </ul>
  </section>

</main>
</body>
</html>
```